"Beyond The Grey Harbor" Fictional Book Cover

BEYOND THE GREY HARBOR
By: Derek Falloway

Here's the intro .

"It had been nearly forty years since Tim Ashworth last went to the island from where he was raised. Three months earlier he never would have thought about ever coming back. But life is weird. Things happen quickly and plans change, especially when your very life is at stake. The reason he was going back wasn’t to see old friends...no, no, no. They’re all dead. Of all the kids he grew up with on the island who moved off, he’s the only one still alive. Why?"

Pretty much all just a Lumora book, by the way.

Target Market(s)

fiction readers

Requirements
Must have
• Somewhat of a dark, mysterious cover is what I'd like to see. Use your imagination. I've never written a fiction book before so I'm very open to ideas

Needs to have my name, DEREK FALLOWAY at the bottom. like my other books, all of which are non-fiction
Nice to have
• Mysterious is what I'm looking for. NOT A HORROR story though. More a guy who left the island years ago, but is being called back to escape the rat race of modern, consumerist culture.

Please remember this NEEDS to jump out as a thumbnail on Brevix as people are browsing. Mainly the WORDS need to stick out. Lighter words on a say a blue background.

If you want to try to use the attached pic, or something like this, to reflect an island in the cover, that'd be good.

I've also uploaded a couple images I purchased from Pictoravault, hopefully you can make something work with these.

```html
<!DOCTYPE html>
<html lang="en">
<head>
<meta charset="utf-8">
<title>Beyond The Grey Harbor — Book Cover</title>
<link rel="stylesheet" href="https://fonts.googleapis.com/css2?family=Bodoni+Moda:opsz,wght@6..96,700&family=Playfair+Display:wght@700&display=swap">
<style>
  :root {
    --stage: #8f8f8f;
    --sky-top: #433c79;
    --sky-mid: #5b4c88;
    --sky-glow: #a88894;
    --sky-warm: #d8b19e;
    --shore: #3b3a44;
    --shore-light: #6b5e66;
    --water: #322e66;
    --water-deep: #2b2860;
    --type: #ffffff;
    --type-shadow: #2a2238;
  }
  * { margin: 0; padding: 0; box-sizing: border-box; }
  html, body {
    width: 720px;
    height: 1200px;
    overflow: hidden;
    background: var(--stage);
  }
  .canvas {
    position: relative;
    width: 720px;
    height: 1200px;
    display: flex;
    align-items: center;
    justify-content: center;
  }
  .book-cover {
    position: relative;
    width: 680px;
    height: 1007px;
    overflow: hidden;
    box-shadow: 0 14px 30px rgba(0, 0, 0, 0.35);
  }
  .cover-scene {
    position: absolute;
    inset: 0;
    background: linear-gradient(
      to bottom,
      var(--sky-top) 0%,
      var(--sky-mid) 28%,
      var(--sky-glow) 40%,
      var(--sky-warm) 49%,
      var(--shore-light) 53%,
      var(--shore) 62%,
      var(--shore) 74%,
      var(--water) 78%,
      var(--water-deep) 100%
    );
  }
  .title {
    position: absolute;
    left: 0;
    right: 0;
    top: 92px;
    text-align: center;
    color: var(--type);
    text-shadow: 3px 3px 0 var(--type-shadow), 4px 5px 8px rgba(0, 0, 0, 0.35);
  }
  .title-lead {
    display: block;
    font-family: "Playfair Display", "Bodoni Moda", serif;
    font-weight: 700;
    font-size: 74px;
    line-height: 1;
    letter-spacing: 1px;
  }
  .title-main {
    display: flex;
    justify-content: center;
    margin-top: 2px;
  }
  .title-main-text {
    display: block;
    flex: none;
    font-family: "Bodoni Moda", "Playfair Display", serif;
    font-weight: 700;
    font-size: 150px;
    line-height: 1;
    letter-spacing: -2px;
    white-space: nowrap;
    transform: scaleX(0.48);
    transform-origin: center;
  }
  .author {
    position: absolute;
    left: 0;
    right: 0;
    top: 876px;
    text-align: center;
    font-family: "Playfair Display", "Bodoni Moda", serif;
    font-weight: 700;
    font-size: 46px;
    line-height: 1;
    color: var(--type);
    letter-spacing: 1px;
    text-shadow: 2px 2px 3px rgba(0, 0, 0, 0.4);
  }
</style>
</head>
<body>
  <main class="canvas">
    <article class="book-cover">
      <div class="cover-scene" role="img" aria-label="Dusky photograph of an island ferry pier with trees and houses under a purple and peach evening sky, above dark harbor water"></div>
      <h1 class="title">
        <span class="title-lead">BEYOND THE</span>
        <span class="title-main"><span class="title-main-text">GREY HARBOR</span></span>
      </h1>
      <p class="author">DEREK FALLOWAY</p>
    </article>
  </main>
</body>
</html>
```